Rehabilitation Centre Driving Evaluation brochure

I have already designed a brochure when I was at my previous workplace, but need a new one for my own rehab clinic. I will attach the brochure that I already did, as the information hasn't really changed. It is just very old and very ugly. It is an information pamphlet that will be in physician offices. Please let me know if you need anything else.

Target Market(s)

physicians, rehabilitation professionals, therapists, and individuals with medical conditions who want to return to driving

Industry/Entity Type

Medical

Requirements
Nice to have
• I am not stuck on the trifold, and actually may prefer a single fold brochure.

```html
<!DOCTYPE html>
<html lang="en">
<head>
<meta charset="utf-8">
<title>Driving Evaluation and Training Center – Brochure</title>
<link rel="stylesheet" href="https://fonts.googleapis.com/css2?family=Oswald:wght@600;700&family=Questrial&display=swap">
<style>
  :root{
    --navy:#1d4568;
    --navy-deep:#15334f;
    --lime:#b3c40e;
    --paper:#ffffff;
    --ink:#3f5a73;
    --muted:#8a98a6;
    --stage:#dcdcdc;
  }
  *{box-sizing:border-box;margin:0;padding:0}
  html,body{width:960px;height:1200px;overflow:hidden;background:var(--stage)}
  body{font-family:"Questrial",sans-serif;color:var(--ink);position:relative}
  .spread{position:absolute;left:30px;width:900px;height:540px;background:var(--paper);box-shadow:0 8px 24px rgba(0,0,0,.18);overflow:hidden}
  .spread--outer{top:40px}
  .spread--inner{top:620px}
  .spread__art{position:absolute;inset:0;width:900px;height:540px}
  .fold{position:absolute;top:0;left:449px;width:2px;height:540px;background:linear-gradient(90deg,rgba(0,0,0,.06),rgba(255,255,255,0))}
  .block{position:absolute}
  .heading{font-size:15px;color:var(--navy);letter-spacing:.3px;margin-bottom:5px}
  .heading--lime{color:var(--lime)}
  .heading--white{color:#fff}
  .copy{font-size:10.2px;line-height:1.42;margin-bottom:8px}
  .copy--white{color:#fff}
  .sub{font-size:11px;color:var(--lime);margin:6px 0 2px}
  .brand{font-size:24px;color:var(--navy);display:flex;align-items:center;gap:10px;letter-spacing:.2px}
  .brand__dot{width:16px;height:16px;border-radius:50%;background:var(--lime);flex:none}
  .brand__line{font-size:11px;color:var(--lime);margin:2px 0 0 26px}
  .contacts{list-style:none;font-size:12px;color:var(--navy);line-height:1.3}
  .contacts li{display:flex;align-items:flex-start;gap:9px;margin-bottom:5px}
  .contacts svg{flex:none;margin-top:1px}
  .cover-title{font-family:"Oswald",sans-serif;font-weight:700;font-size:28px;line-height:1.02;letter-spacing:-.2px;text-transform:uppercase}
  .cover-title span{display:block}
  .cover-title .t1{color:var(--navy)}
  .cover-title .t2{color:var(--lime);padding-left:10px}
  .tagline{font-size:15px;color:var(--navy);line-height:1.15}
  .tagline span{display:block;color:var(--lime);padding-left:28px}
  .url{font-size:10px;color:var(--muted)}
  .url--vertical{transform:rotate(90deg);transform-origin:left top;color:#6d8aa3}
</style>
</head>
<body>

<section class="spread spread--outer" aria-label="Brochure outside">
  <svg class="spread__art" viewBox="0 0 900 540">
    <defs>
      <linearGradient id="roadScene" x1="0" y1="0" x2="0.6" y2="1">
        <stop offset="0" stop-color="#f7f6f3"/>
        <stop offset=".35" stop-color="#e2e0da"/>
        <stop offset=".65" stop-color="#8d8a82"/>
        <stop offset="1" stop-color="#3e3e3e"/>
      </linearGradient>
      <linearGradient id="navyFade" x1="0" y1="0" x2="1" y2="1">
        <stop offset="0" stop-color="#1d4568"/>
        <stop offset=".7" stop-color="#2b5a80"/>
        <stop offset="1" stop-color="#1d4568"/>
      </linearGradient>
    </defs>
    <rect x="450" y="0" width="450" height="380" fill="url(#roadScene)" role="img" aria-label="Photo: open highway stretching toward desert mountains with yellow centre line"/>
    <path d="M870,180 L900,175 L900,380 L820,380 Z" fill="#c9a21f" opacity=".7"/>
    <path d="M0,0 H450 V300 C380,250 250,250 140,268 C80,278 30,290 0,300 Z" fill="url(#navyFade)"/>
    <path d="M450,0 H540 C545,150 690,260 900,330 V380 C760,360 560,300 450,300 Z" fill="var(--navy)"/>
    <path d="M505,0 H525 C535,150 640,250 830,320 C640,270 515,170 505,0 Z" fill="var(--lime)"/>
    <path d="M450,300 C560,300 760,360 900,380 V540 H450 Z" fill="#fff"/>
  </svg>
  <div class="fold"></div>

  <div class="block" style="left:40px;top:36px;width:380px">
    <h3 class="heading heading--lime">Referral Process</h3>
    <p class="copy copy--white">Referrals maybe made by physicians, therapists, individuals requiring service, insurance companies, case managers, community service agencies, etc. The referral source will be asked to complete a referral form. The client's physician will be contacted and asked to complete a medical referral form stating the client is medically able to participate in the assessment.</p>
    <p class="copy copy--white">Referrals can be made for any individual who requires an evaluation of their driving skills or adaptive equipment needs by contacting us.</p>
  </div>

  <div class="block" style="left:56px;top:350px;width:360px">
    <div class="brand"><span class="brand__dot"></span>Meridian Rehab Partners</div>
    <ul class="contacts" style="margin-top:16px;margin-left:4px">
      <li><svg width="12" height="14" viewBox="0 0 12 14"><path d="M6 1a4 4 0 0 1 4 4c0 3-4 8-4 8S2 8 2 5a4 4 0 0 1 4-4z" fill="none" stroke="#b3c40e" stroke-width="1.5"/><circle cx="6" cy="5" r="1.4" fill="#b3c40e"/></svg><span>420 Harbour Lane, Unit #5<br>Brookfield, Ontario, N0R 2B4</span></li>
      <li><svg width="12" height="12" viewBox="0 0 12 12"><path d="M2 1h3l1 3-2 1a7 7 0 0 0 3 3l1-2 3 1v3c-6 0-10-4-9-9z" fill="#b3c40e"/></svg><span>555 014 2287</span></li>
      <li><svg width="12" height="12" viewBox="0 0 12 12"><rect x="3" y="1" width="6" height="3" fill="#b3c40e"/><rect x="1" y="4" width="10" height="5" rx="1" fill="#b3c40e"/><rect x="3" y="8" width="6" height="3" fill="#b3c40e"/></svg><span>555 014 2288</span></li>
      <li><svg width="13" height="11" viewBox="0 0 13 11"><rect x="1" y="1" width="11" height="9" fill="none" stroke="#b3c40e" stroke-width="1.4"/><path d="M1 1l5.5 5L12 1" fill="none" stroke="#b3c40e" stroke-width="1.4"/></svg><span>office@meridianrehab.ca</span></li>
      <li><svg width="12" height="12" viewBox="0 0 12 12"><circle cx="6" cy="6" r="5" fill="none" stroke="#b3c40e" stroke-width="1.4"/><path d="M1 6h10M6 1c-3 3-3 7 0 10M6 1c3 3 3 7 0 10" fill="none" stroke="#b3c40e" stroke-width="1"/></svg><span>www.meridianrehab.ca</span></li>
    </ul>
  </div>

  <h1 class="block cover-title" style="left:590px;top:40px">
    <span class="t1">Driving Evaluation</span>
    <span class="t2">and Training Center</span>
  </h1>

  <div class="block" style="left:500px;top:400px;width:380px">
    <div class="brand"><span class="brand__dot"></span>Meridian Rehab Partners</div>
    <p class="brand__line">Driver Rehabilitation Services</p>
  </div>
  <p class="block tagline" style="left:520px;top:460px">A comprehensive<span>driver rehabilitation program</span></p>
  <p class="block url" style="left:520px;top:515px">www.meridianrehab.ca</p>
</section>

<section class="spread spread--inner" aria-label="Brochure inside">
  <svg class="spread__art" viewBox="0 0 900 540">
    <defs>
      <linearGradient id="fadedRoad" x1="0" y1="0" x2="0" y2="1">
        <stop offset="0" stop-color="#ffffff"/>
        <stop offset=".6" stop-color="#f1f1ef"/>
        <stop offset="1" stop-color="#e4e2dc"/>
      </linearGradient>
      <linearGradient id="mistRoad" x1="0" y1="0" x2="0.4" y2="1">
        <stop offset="0" stop-color="#d7d7d7"/>
        <stop offset=".5" stop-color="#9a9a9a"/>
        <stop offset="1" stop-color="#5c5c5c"/>
      </linearGradient>
      <linearGradient id="wheel" x1="0" y1="0" x2="1" y2="1">
        <stop offset="0" stop-color="#e9e5dc"/>
        <stop offset=".5" stop-color="#8c8a86"/>
        <stop offset="1" stop-color="#2d2f33"/>
      </linearGradient>
    </defs>
    <rect x="0" y="0" width="450" height="540" fill="url(#fadedRoad)" role="img" aria-label="Faded photo: quiet country road"/>
    <path d="M330,0 H350 C370,170 470,280 640,320 C460,300 350,180 330,0 Z" fill="var(--lime)"/>
    <path d="M350,0 H505 C520,150 570,250 640,310 C470,280 370,170 350,0 Z" fill="url(#mistRoad)" role="img" aria-label="Photo: car driving along a misty road"/>
    <path d="M505,0 H900 V340 C820,370 720,365 640,310 C570,250 520,150 505,0 Z" fill="var(--navy)"/>
    <circle cx="812" cy="405" r="72" fill="var(--lime)"/>
    <circle cx="812" cy="405" r="66" fill="#fff"/>
    <circle cx="812" cy="405" r="62" fill="url(#wheel)" role="img" aria-label="Photo: hands on a car steering wheel"/>
  </svg>
  <div class="fold"></div>

  <div class="block" style="left:34px;top:46px;width:330px">
    <h3 class="heading">Reason for Assessment</h3>
    <p class="copy">Each physician is required by law to report to the Ministry of Transportation any individual whose driving skills maybe affected as a result of illness or injury. Therefore, the client's driver's licence maybe placed under medical suspension. If this occurs, the client will be asked to undergo a driving evaluation from an approved Driver Assessment Centre.</p>
    <p class="copy">Individuals affected by illness, injury, or the aging process, whose driving skills have the potential to be affected, are also encouraged to undergo an evaluation of driving skills. The evaluation is designed to assess each client's ability to safely operate a motor vehicle and provide recommendations as needed.</p>
  </div>
  <div class="block" style="left:34px;top:252px;width:400px">
    <h3 class="heading">Eligibility</h3>
    <p class="copy">Most individuals with disabilities are eligible for an evaluation of their ability to drive. Clients must have a valid driver's licence or the ability to obtain a temporary driver's licence or learner's permit.</p>
  </div>
  <div class="block" style="left:34px;top:330px;width:400px">
    <h3 class="heading">What we do?</h3>
    <p class="copy">Meridian Rehab Partners is committed to providing optimal rehabilitation service in a cost effective manner.</p>
    <p class="copy">We offer a multi-disciplinary, client-centred program of assessment, treatment and consultation for clients with physical, cognitive and/or perceptual impairments. We are aware each client is unique, therefore each program is tailored according to the individual's needs and personal goals.</p>
    <p class="copy">The driving assessment and training program is part of our comprehensive rehabilitation services. It is a service which represents our dedication to assist all individuals achieve optimal independence. Driving is an integral skill which is often essential for independence in the community.</p>
  </div>

  <div class="block" style="left:560px;top:22px;width:310px">
    <h3 class="heading heading--white">Program Components &amp; Services</h3>
    <p class="sub">Clinical Evaluation</p>
    <p class="copy copy--white">The client is assessed by a certified occupational therapist. The client is first seen in clinic for an assessment of physical, cognitive and perceptual functioning as they relate to driving. The in-clinic portion gives the therapist information on medical history, driving history, road rules, physical abilities, cognitive status, visual and perceptual skills.</p>
    <p class="sub">On the Road Evaluation</p>
    <p class="copy copy--white">Following the in-clinic assessment, each client is assessed in car by the therapist together with a certified driving instructor. This portion of the evaluation provides valuable information on the individual's functional driving skills.</p>
  </div>
  <div class="block" style="left:655px;top:228px;width:225px">
    <p class="sub">Evaluation Equipment Needs</p>
    <p class="copy copy--white" style="font-size:9.6px">During the evaluation, it will be determined whether adaptive equipment is necessary to improve the client's ability to drive safely. Recommendations will be made for equipment and installation.</p>
  </div>

  <div class="block" style="left:480px;top:380px;width:230px">
    <h3 class="heading" style="font-size:12.5px">Training &amp; Follow-up Services</h3>
    <p class="copy">Clients are commonly seen following a driving evaluation for training with driving skills or adaptive equipment. Further involvement with the occupational therapist maybe indicated for cognitive or perceptual retraining, mobility-aid prescription, vehicle modification, or consultation with appropriate new vehicle purchase.</p>
  </div>
  <p class="block url url--vertical" style="left:892px;top:120px">www.meridianrehab.ca</p>
</section>

</body>
</html>
```